I need a fresh looking, exciting and loaded design for Full service Restaurant

We need a web design for our restaurant, which offers full service Pakistani and Indian food in PA, USA. Design should be elegant, simplified so customers can navigate easily and order food online for catering as well as delivery. We need loads of pictures and room to grow. I already have a web address via vemrilo.com. It should include SSL and e-commerce for ordering food.
Be original and be creative and make it a fun site :)

```html
<!DOCTYPE html>
<html lang="en">
<head>
<meta charset="utf-8">
<title>Saffron Lane – Pakistani &amp; Indian Restaurant</title>
<link href="https://fonts.googleapis.com/css2?family=Great+Vibes&family=Open+Sans:wght@400;600;700&display=swap" rel="stylesheet">
<style>
:root{
  --paper:#efe7da;
  --paper-dark:#e4dac9;
  --red:#d92b26;
  --red-dark:#b81f1b;
  --ink:#3a3330;
  --muted:#7a716b;
  --white:#ffffff;
  --night:#2f2f2f;
  --line:#d8cdbb;
}
*{box-sizing:border-box;margin:0;padding:0}
html,body{width:1200px;height:3208px;overflow:hidden}
body{background:var(--paper);font-family:"Open Sans",Arial,sans-serif;color:var(--ink)}
.page{position:relative;width:1200px;height:3208px}
.abs{position:absolute}
.script{font-family:"Great Vibes",cursive;font-weight:400}
.photo{position:absolute;border-radius:2px}

/* header */
.brand{left:96px;top:22px;display:flex;align-items:center;gap:12px}
.brand-dot{width:46px;height:46px;border-radius:50%;background:var(--red)}
.brand-name{font-family:"Open Sans",Arial,sans-serif;font-weight:700;font-size:30px;color:var(--red)}
.brand-tag{left:154px;top:68px;font-size:11px;color:var(--muted);letter-spacing:1px}
.search{left:690px;top:22px;width:210px;height:30px;background:var(--white);border:1px solid var(--line);font-size:12px;color:var(--muted);padding:6px 10px}
.util{top:28px;font-size:12px;color:var(--muted)}
.nav{left:520px;top:82px;display:flex;height:36px}
.nav a{display:block;padding:0 16px;line-height:36px;font-size:13px;font-weight:600;color:var(--ink);text-decoration:none;border-right:1px solid var(--line)}
.nav a:last-child{border-right:none}
.nav a.active{background:var(--red);color:var(--white)}

/* hero */
.hero-frame{left:118px;top:168px;width:964px;height:480px;background:var(--white);padding:12px;box-shadow:0 2px 6px rgba(0,0,0,.12)}
.hero-photo{left:12px;top:12px;width:940px;height:456px;background:linear-gradient(120deg,#3b2a20 0%,#6b4a30 35%,#8a3b26 60%,#4a3426 100%)}
.hero-caption{left:100px;top:460px;width:380px;height:110px;background:var(--red);color:var(--white);padding:14px 22px}
.hero-caption h2{font-size:34px;line-height:1}
.hero-caption p{font-size:12px;margin-top:8px;line-height:1.5}
.arrow{width:36px;height:36px;border-radius:50%;background:rgba(255,255,255,.85);top:390px}

/* headings */
.section-title{width:1200px;left:0;text-align:center;font-size:44px;color:var(--ink)}
.intro{left:250px;top:790px;width:700px;text-align:center;font-size:13px;line-height:1.7;color:var(--muted)}

/* cards */
.card{top:912px;width:304px;height:480px;background:var(--white);box-shadow:0 1px 4px rgba(0,0,0,.1);text-align:center}
.card h3{font-size:38px;color:var(--red);margin-top:16px}
.card .photo{left:16px;top:86px;width:272px;height:176px}
.dish-curry{background:linear-gradient(135deg,#f1d7a8 0%,#d98a3a 45%,#a8401f 100%)}
.dish-breakfast{background:linear-gradient(135deg,#f6efe3 0%,#f0c86a 45%,#b9673a 100%)}
.dish-grill{background:linear-gradient(135deg,#5a3a26 0%,#8e4a2a 50%,#e0b040 100%)}
.card p{position:absolute;left:24px;top:290px;width:256px;font-size:12px;line-height:1.7;color:var(--muted)}
.btn{display:inline-block;background:var(--red);color:var(--white);font-size:11px;font-weight:700;letter-spacing:.5px;padding:8px 16px}
.card .btn{position:absolute;left:112px;top:412px}

/* meal of the day */
.meal{top:1540px;width:500px;height:180px}
.meal .photo{left:0;top:20px;width:170px;height:110px;border-radius:50%}
.dish-soup{background:radial-gradient(ellipse at 50% 40%,#c88a3a 0%,#a36a2a 35%,#f4f1ec 60%,#d9d3c9 100%)}
.dish-fish{background:radial-gradient(ellipse at 50% 40%,#8a5a34 0%,#5a3a22 35%,#f2eee8 62%,#cfc8bd 100%)}
.meal h4{position:absolute;left:200px;top:20px;font-size:17px;font-weight:700}
.meal p{position:absolute;left:200px;top:52px;width:270px;font-size:12px;line-height:1.6;color:var(--muted)}
.meal .btn{position:absolute;left:200px;top:118px}

/* gallery */
.gallery{left:108px;top:1780px;width:992px;height:580px;background:var(--white);box-shadow:0 1px 4px rgba(0,0,0,.1)}
.gallery .photo{width:300px;height:210px}

/* bottom */
.map{left:530px;top:2430px;width:570px;height:400px;background:linear-gradient(135deg,#e9eef1,#d7e3e8 60%,#cfe0d2)}
.map-info{left:560px;top:2456px;width:200px;background:var(--white);padding:10px 12px;font-size:11px;line-height:1.5;color:var(--muted);box-shadow:0 1px 3px rgba(0,0,0,.2)}
.map-info strong{color:var(--red);font-size:11px}
.subscribe{left:108px;top:2830px;width:992px;height:170px;background:var(--night)}
.subscribe h3{position:absolute;left:40px;top:22px;font-size:40px;color:var(--white)}
.subscribe .field{position:absolute;left:40px;top:98px;width:760px;height:44px;border:1px solid #5a5a5a;color:#9a9a9a;font-size:13px;padding:12px 16px}
.subscribe .btn{position:absolute;left:820px;top:98px;height:44px;width:140px;font-size:13px;text-align:center;line-height:28px}

.social{left:528px;top:3040px;display:flex;gap:12px}
.social span{width:30px;height:30px;background:var(--ink);border-radius:3px;display:block}
.copyright{left:0;width:1200px;top:3096px;text-align:center;font-size:12px;color:var(--muted)}
</style>
</head>
<body>
<div class="page">

  <header>
    <div class="abs brand"><span class="brand-dot"></span><span class="brand-name">Saffron Lane</span></div>
    <div class="abs brand-tag">INDIAN &amp; PAKISTANI CUISINE</div>
    <div class="abs search">Search</div>
    <div class="abs util" style="left:950px">&#128722; Your Cart</div>
    <div class="abs util" style="left:1040px">&#128100; Sign In</div>
    <nav class="abs nav">
      <a class="active" href="#">SPECIALS</a><a href="#">MENU</a><a href="#">ENTERTAINMENT</a><a href="#">HOME DELIVERY</a><a href="#">ABOUT</a><a href="#">CONTACT</a>
    </nav>
  </header>

  <section class="abs hero-frame">
    <div class="photo hero-photo" role="img" aria-label="Grilled steak, vegetables and spices on a wooden board"></div>
  </section>
  <div class="abs arrow" style="left:134px">
    <svg width="36" height="36" viewBox="0 0 36 36"><path d="M21 11l-7 7 7 7" fill="none" stroke="#555" stroke-width="2.5"/></svg>
  </div>
  <div class="abs arrow" style="left:1030px">
    <svg width="36" height="36" viewBox="0 0 36 36"><path d="M15 11l7 7-7 7" fill="none" stroke="#555" stroke-width="2.5"/></svg>
  </div>
  <div class="abs hero-caption">
    <h2 class="script">Saffron Lane Foods</h2>
    <p>Fresh spices, slow-cooked grills and family recipes served daily at our table.</p>
  </div>

  <h2 class="abs section-title script" style="top:712px">Welcome to Saffron Lane</h2>
  <p class="abs intro">Our kitchen brings the warm flavors of Pakistan and India to Pennsylvania, with curries, kebabs and breads made fresh every day. Join us for dinner, order catering for your next event or get your favorites delivered hot to your door.</p>

  <article class="abs card" style="left:108px">
    <h3 class="script">Indian Spice</h3>
    <div class="photo dish-curry" role="img" aria-label="Plate of Indian curry with rice"></div>
    <p>Rich curries, tandoori grills and fragrant rice dishes prepared with whole spices ground in our kitchen every morning for deep, honest flavor.</p>
    <span class="btn">READ MORE</span>
  </article>
  <article class="abs card" style="left:448px">
    <h3 class="script">Pakistani food</h3>
    <div class="photo dish-breakfast" role="img" aria-label="Breakfast plate with eggs and bread"></div>
    <p>Karahi, nihari and seekh kebabs from Lahore and Karachi, cooked the traditional way and served with warm naan straight from the oven.</p>
    <span class="btn">READ MORE</span>
  </article>
  <article class="abs card" style="left:788px">
    <h3 class="script">Splendid Menu</h3>
    <div class="photo dish-grill" role="img" aria-label="Grilled meat with lemon and greens"></div>
    <p>Seasonal plates, chef specials and generous platters built for sharing, with options for every table and every appetite in the family.</p>
    <span class="btn">READ MORE</span>
  </article>

  <h2 class="abs section-title script" style="top:1448px">Meal of the day</h2>
  <div class="abs meal" style="left:108px">
    <div class="photo dish-soup" role="img" aria-label="Bowl of sour cherry soup"></div>
    <h4>Sour cherry soup</h4>
    <p>A light, tangy soup with cherries, herbs and a hint of cumin, served warm with fresh bread.</p>
    <span class="btn">CHECK OTHER SOUPS &#8250;</span>
  </div>
  <div class="abs meal" style="left:620px">
    <div class="photo dish-fish" role="img" aria-label="Bowl of oak-grilled fish"></div>
    <h4>Oak fish a la Pali</h4>
    <p>Grilled fish marinated in lemon, garlic and green chili, finished over oak and served with rice.</p>
    <span class="btn">CHECK OTHER MEALS &#8250;</span>
  </div>

  <section class="abs gallery">
    <h2 class="abs section-title script" style="width:992px;top:24px">Feel how it's inside</h2>
    <div class="photo" style="left:20px;top:96px;background:linear-gradient(135deg,#2a1a12,#a0451d)" role="img" aria-label="Meat grilling over flames"></div>
    <div class="photo" style="left:346px;top:96px;background:linear-gradient(135deg,#c97a3c,#7a3a22)" role="img" aria-label="Seafood platter with lobster"></div>
    <div class="photo" style="left:672px;top:96px;background:linear-gradient(135deg,#3a2418,#8a3a26)" role="img" aria-label="Sliced steak with vegetables"></div>
    <div class="photo" style="left:20px;top:326px;background:linear-gradient(135deg,#d9a373,#b4502e)" role="img" aria-label="Plated shrimp dish"></div>
    <div class="photo" style="left:346px;top:326px;background:linear-gradient(135deg,#3b2c1f,#9c5a2b)" role="img" aria-label="Roast chicken on a table"></div>
    <div class="photo" style="left:672px;top:326px;background:linear-gradient(135deg,#caa070,#8d4a26)" role="img" aria-label="Grilled chicken with herbs"></div>
  </section>

  <div class="photo" style="left:100px;top:2400px;width:390px;height:430px;background:linear-gradient(180deg,#e8e2da,#cbb9a8)" role="img" aria-label="Guest holding a red chili pepper"></div>
  <div class="abs map" role="img" aria-label="Street map of the restaurant area"></div>
  <div class="abs map-info"><strong>SAFFRON LANE</strong><br>1250 Market Street, Suite 4,<br>Philadelphia, PA 19107</div>
  <svg class="abs" style="left:795px;top:2520px" width="44" height="60" viewBox="0 0 44 60"><path d="M22 2C11 2 3 10 3 21c0 14 19 37 19 37s19-23 19-37C41 10 33 2 22 2z" fill="#d92b26"/><circle cx="22" cy="21" r="7" fill="#fff"/></svg>

  <section class="abs subscribe">
    <h3 class="script">Subscribe for Updates</h3>
    <div class="field">Enter your email address here</div>
    <span class="btn">SUBSCRIBE</span>
  </section>

  <footer>
    <div class="abs social"><span></span><span></span><span></span><span></span></div>
    <p class="abs copyright">© Saffron Lane 2013-2016 - saffronlane-web.com - All rights reserved</p>
  </footer>
</div>
</body>
</html>
```